Web design

We need the design for the logo and website for a women fashion website. No coding required. The colors used should be neutral (maybe with a light touch of color), the style should be modern, slightly luxurious, not too crowded. The target market is young professionals who love trendy clothes.
Updates

Need extra days to review

Target Market(s)

Young professionals

Industry/Entity Type

Apparel

Number of Pages Required

5+ page

Font styles to use
Sans Serif
Other font styles liked:
• Montserrat, Engravers Gothic, Benton Sans, gotham-book

Colors

Designer to choose colors to be used in the design.

```html
<!DOCTYPE html>
<html lang="en">
<head>
<meta charset="utf-8">
<title>NAVE — Checkout</title>
<link href="https://fonts.googleapis.com/css2?family=Montserrat:wght@400;500;600&family=Roboto:wght@400;500&display=swap" rel="stylesheet">
<style>
:root{
  --ink:#1c1c1c;
  --muted:#6b6b6b;
  --faint:#b9b9b9;
  --line:#cfcfcf;
  --gold:#d4a20e;
  --teal:#7fcdbb;
  --sale:#e8362b;
  --footer:#f3f2f0;
  --navy:#1e1c33;
}
*{box-sizing:border-box;margin:0;padding:0}
html,body{width:968px;height:1200px;overflow:hidden;background:#fff}
body{position:relative;font-family:'Roboto',Arial,sans-serif;color:var(--ink)}

/* header */
.site-header{position:absolute;left:0;top:0;width:968px;height:61px;border-bottom:1px solid #e3e3e3}
.nav-link{position:absolute;top:24px;font-size:12.5px;color:var(--ink);white-space:nowrap}
.nav-link.sale{color:var(--sale)}
.brand-name{position:absolute;left:448px;top:27px;width:100px;text-align:center;font-family:'Montserrat',sans-serif;font-weight:500;font-size:22px;letter-spacing:1px;color:var(--navy);line-height:26px}
.lang{position:absolute;left:777px;top:27px;font-size:9.5px}
.tool-icon{position:absolute;top:22px}

/* title & steps */
.page-title{position:absolute;left:0;width:968px;top:110px;text-align:center;font-family:'Montserrat',sans-serif;font-weight:600;font-size:33px;letter-spacing:1px}
.step-dot{position:absolute;top:173px;width:33px;height:33px;border-radius:50%;background:#e2e2e2;color:#fff;font-family:'Montserrat',sans-serif;font-weight:500;font-size:17px;line-height:33px;text-align:center}
.step-dot.active{background:var(--gold)}
.step-label{position:absolute;top:183px;font-size:11.5px;color:var(--faint);font-weight:500;white-space:nowrap}
.step-label.active{color:var(--ink)}

/* section headings */
.section-title{position:absolute;top:272px;font-family:'Montserrat',sans-serif;font-weight:600;font-size:24px;letter-spacing:.5px}
.rule{position:absolute;top:309px;height:1px;background:#d8d8d8}
.rule-accent{position:absolute;top:308px;height:1.5px;background:var(--teal)}

/* form */
.field-label{position:absolute;left:83px;font-family:'Montserrat',sans-serif;font-size:9.8px;color:var(--muted);letter-spacing:.3px}
.field-label sup{color:var(--teal);font-size:7px}
.field{position:absolute;left:190px;width:287px;height:35px;border:1px solid var(--line);background:#fff;font-size:10.5px;color:var(--muted);padding:0 10px;line-height:33px}
.field .caret{position:absolute;right:10px;top:14px;width:0;height:0;border-left:5px solid transparent;border-right:5px solid transparent;border-top:6px solid #3a3a3a}

/* order */
.order-text{position:absolute;font-family:'Montserrat',sans-serif;font-weight:600;font-size:14.5px;letter-spacing:.3px}
.order-val{position:absolute;left:772px;font-size:14.5px}
.qty-box{position:absolute;left:768px;top:368px;width:59px;height:30px;border:1px solid var(--line);text-align:center;line-height:30px;font-size:14px}
.hr{position:absolute;left:527px;width:366px;height:1px;background:#dadada}
.edit-btn{position:absolute;left:835px;top:476px;width:53px;height:20px;border-radius:10px;background:var(--gold);color:#fff;font-size:6.5px;font-weight:500;text-align:center;line-height:20px}
.radio{position:absolute;left:529px;width:13px;height:13px;border:1.3px solid var(--ink);border-radius:50%}
.radio.on::after{content:"";position:absolute;left:2.5px;top:2.5px;width:5.5px;height:5.5px;border-radius:50%;background:var(--ink)}
.radio-text{position:absolute;left:549px;font-family:'Montserrat',sans-serif;font-weight:500;font-size:14.5px}
.pay-badge{position:absolute;top:602px;width:48px;height:30px;border-radius:3px}
.card-label{position:absolute;font-size:10.5px;color:var(--muted)}
.card-field{position:absolute;height:35px;border:1px solid var(--line);background:#fff}
.add-card{position:absolute;left:750px;top:752px;width:107px;height:35px;background:var(--ink);color:#fff;font-size:10.5px;font-weight:500;text-align:center;line-height:35px}
.continue{position:absolute;left:743px;top:823px;width:144px;height:41px;background:var(--gold);color:#fff;font-size:15px;font-weight:500;text-align:center;line-height:41px;border-radius:1px}

/* footer */
.site-footer{position:absolute;left:0;top:927px;width:968px;height:273px;background:var(--footer)}
.foot-name{position:absolute;left:50px;width:200px;top:1040px;text-align:center;font-family:'Montserrat',sans-serif;font-weight:500;font-size:44px;color:var(--navy);letter-spacing:1px}
.foot-head{position:absolute;top:991px;font-family:'Montserrat',sans-serif;font-weight:600;font-size:12.5px;letter-spacing:.5px}
.foot-link{position:absolute;font-family:'Montserrat',sans-serif;font-size:10.6px;color:#333;letter-spacing:.3px}
.social-dot{position:absolute;left:767px;width:8px;height:8px;border-radius:50%;background:var(--ink)}
.foot-rule{position:absolute;left:90px;top:1146px;width:787px;height:1px;background:#d6d6d6}
.copyright{position:absolute;left:0;width:968px;top:1160px;text-align:center;font-family:'Montserrat',sans-serif;font-size:10.6px;color:#333}
</style>
</head>
<body>

<header class="site-header">
  <span class="nav-link" style="left:83px">Latest Arrivals</span>
  <span class="nav-link" style="left:179px">Clothes &#8964;</span>
  <span class="nav-link" style="left:253px">NAVE Club</span>
  <span class="nav-link sale" style="left:335px">On Sale</span>
  <div class="brand-name">NAVE</div>
  <svg class="tool-icon" style="left:741px" width="14" height="14" viewBox="0 0 14 14" fill="none" stroke="#1c1c1c" stroke-width="1.3"><circle cx="6" cy="6" r="4.8"/><path d="M9.5 9.5L13 13"/></svg>
  <span class="lang">ENG &#8964;</span>
  <svg class="tool-icon" style="left:814px;top:24px" width="20" height="18" viewBox="0 0 20 18" fill="none" stroke="#1c1c1c" stroke-width="1.4"><path d="M10 16.5S1.5 11 1.5 5.6A4.2 4.2 0 0 1 10 3.8a4.2 4.2 0 0 1 8.5 1.8C18.5 11 10 16.5 10 16.5z"/></svg>
  <svg class="tool-icon" style="left:840px" width="18" height="20" viewBox="0 0 18 20" fill="none" stroke="#1c1c1c" stroke-width="1.3"><circle cx="9" cy="6" r="4.5"/><path d="M1 19.5c0-4.5 3.6-7.5 8-7.5s8 3 8 7.5"/></svg>
  <svg class="tool-icon" style="left:866px;top:23px" width="18" height="20" viewBox="0 0 18 20" fill="none" stroke="#1c1c1c" stroke-width="1.3"><rect x="1.5" y="6" width="15" height="13" rx="1"/><path d="M5.5 8V4.5a3.5 3.5 0 0 1 7 0V8"/></svg>
  <svg class="tool-icon" style="left:876px;top:23px" width="11" height="11"><circle cx="5.5" cy="5.5" r="5" fill="#d4a20e"/><text x="5.5" y="8.2" font-size="7" fill="#fff" text-anchor="middle" font-family="Roboto,sans-serif">0</text></svg>
</header>

<main>
  <h1 class="page-title">CHECKOUT</h1>

  <div class="step-dot active" style="left:156px">1</div><span class="step-label active" style="left:201px">BILLING DETAILS</span>
  <div class="step-dot" style="left:328px">2</div><span class="step-label" style="left:373px">SHIPPING DETAILS</span>
  <div class="step-dot" style="left:510px">3</div><span class="step-label" style="left:556px">REVIEW &amp; PAYMENT</span>
  <div class="step-dot" style="left:699px">4</div><span class="step-label" style="left:745px">CONIRMATION</span>

  <section class="billing">
    <h2 class="section-title" style="left:83px">BILLING ADDRESS</h2>
    <div class="rule" style="left:83px;width:367px"></div>
    <div class="rule-accent" style="left:83px;width:228px"></div>

    <span class="field-label" style="top:345px">BILLING PROFILE<sup>*</sup></span>
    <div class="field" style="top:333px">New Billing Profile<span class="caret"></span></div>
    <span class="field-label" style="top:388px">FIRST NAME<sup>*</sup></span>
    <div class="field" style="top:376px"></div>
    <span class="field-label" style="top:431px">LAST NAME<sup>*</sup></span>
    <div class="field" style="top:419px"></div>
    <span class="field-label" style="top:473px">ADDRESS LINE1<sup>*</sup></span>
    <div class="field" style="top:461px"></div>
    <span class="field-label" style="top:516px">ADDRESS LINE2<sup>*</sup></span>
    <div class="field" style="top:504px"></div>
    <span class="field-label" style="top:559px">CITY<sup>*</sup></span>
    <div class="field" style="top:546px">- - - - Select - - - -<span class="caret"></span></div>
    <span class="field-label" style="top:602px">STATE</span>
    <div class="field" style="top:589px">- - - - Select - - - -<span class="caret"></span></div>
    <span class="field-label" style="top:645px">POSTCODE</span>
    <div class="field" style="top:632px"></div>
    <span class="field-label" style="top:687px">COUNTRY</span>
    <div class="field" style="top:675px">- - - - Select - - - -<span class="caret"></span></div>
    <span class="field-label" style="top:730px">EMAIL<sup>*</sup></span>
    <div class="field" style="top:718px"></div>
    <span class="field-label" style="top:773px">PHONE</span>
    <div class="field" style="top:761px"></div>
  </section>

  <section class="order">
    <h2 class="section-title" style="left:525px">YOUR ORDER</h2>
    <div class="rule" style="left:527px;width:366px"></div>
    <div class="rule-accent" style="left:527px;width:229px"></div>

    <span class="order-text" style="left:529px;top:330px">The standard Ipsum passage</span>
    <span class="order-val" style="top:330px">$25.00</span>
    <span class="order-text" style="left:529px;top:373px">Quantity:</span>
    <div class="qty-box">1</div>
    <span class="order-text" style="left:529px;top:419px">Shipping:</span>
    <span class="order-val" style="top:419px">FREE</span>
    <div class="hr" style="top:462px"></div>
    <span class="order-text" style="left:529px;top:479px">Total:</span>
    <span class="order-val" style="top:479px">$25.00</span>
    <div class="edit-btn">EDIT &gt;&gt;</div>
    <div class="hr" style="top:513px"></div>

    <span class="radio" style="top:538px"></span><span class="radio-text" style="top:535px">Cash on delivery</span>
    <span class="radio on" style="top:568px"></span><span class="radio-text" style="top:565px">Credit and Debit cards</span>

    <div class="pay-badge" role="img" aria-label="Payment option badge" style="left:529px;background:#e9e9e9"></div>
    <div class="pay-badge" role="img" aria-label="Payment option badge" style="left:582px;background:#ececec"></div>
    <div class="pay-badge" role="img" aria-label="Payment option badge" style="left:636px;background:#2f6f9f"></div>
    <div class="pay-badge" role="img" aria-label="Payment option badge" style="left:689px;background:linear-gradient(135deg,#eeeeee 55%,#f0a040)"></div>
    <div class="pay-badge" role="img" aria-label="Payment option badge" style="left:743px;background:#3d9ad8"></div>

    <span class="card-label" style="left:530px;top:663px">NAME ON CARD</span>
    <span class="card-label" style="left:662px;top:663px">CARD NUMBER</span>
    <div class="card-field" style="left:531px;top:685px;width:127px"></div>
    <div class="card-field" style="left:663px;top:685px;width:195px"></div>
    <span class="card-label" style="left:530px;top:730px">EXPIRY DATE</span>
    <span class="card-label" style="left:662px;top:730px">CVV</span>
    <div class="card-field" style="left:531px;top:752px;width:127px"></div>
    <div class="card-field" style="left:663px;top:752px;width:79px"></div>
    <div class="add-card">ADD YOUR CARD</div>

    <div class="continue">CONTINUE &gt;&gt;</div>
  </section>
</main>

<footer class="site-footer"></footer>
<div class="foot-name">NAVE</div>

<h3 class="foot-head" style="left:324px">HELP</h3>
<span class="foot-link" style="left:323px;top:1024px">Email Address</span>
<span class="foot-link" style="left:323px;top:1045px">Returns/exchanges</span>
<span class="foot-link" style="left:323px;top:1067px">Delivery Information</span>
<span class="foot-link" style="left:323px;top:1088px">FAQ</span>

<h3 class="foot-head" style="left:534px">SHOP</h3>
<span class="foot-link" style="left:533px;top:1024px">Tops</span>
<span class="foot-link" style="left:533px;top:1045px">Bootoms</span>
<span class="foot-link" style="left:533px;top:1067px">Intimates</span>
<span class="foot-link" style="left:533px;top:1088px">Dresses</span>
<span class="foot-link" style="left:533px;top:1110px">Swim</span>

<h3 class="foot-head" style="left:763px">FOLLOW US</h3>
<span class="social-dot" style="top:1027px"></span><span class="foot-link" style="left:788px;top:1024px">Facelane</span>
<span class="social-dot" style="top:1048px"></span><span class="foot-link" style="left:788px;top:1045px">Chirper</span>
<span class="social-dot" style="top:1070px"></span><span class="foot-link" style="left:788px;top:1067px">Snapgrid</span>
<span class="social-dot" style="top:1091px"></span><span class="foot-link" style="left:788px;top:1088px">Worklink</span>

<div class="foot-rule"></div>
<p class="copyright">Terms &amp; Conditions, Privacy Policy and @2021 followed by nave.</p>

</body>
</html>
```